Varnik Holdings — Business Card Design Brief
Overview
Design a double-sided business card for Varnik Holdings that highlights our two service arms: Varnik Communications (telecommunications) and Varnik Energy (business energy solutions). The card should feel smart and stand out when handed to clients.

Objectives
Showcase our areas of specialty clearly.
Reflect the overall Varnik / Varnik Holdings brand while acknowledging both arms.
Explore using both logos (Communications + Energy) or one unified logo, depending on the design.

Deliverables
One double-sided business card design (front + back).

Content & Copy
Front (preferred): Logo: Varnik / Varnik Holdings
Descriptor: Business Communications | Business Energy
Back:My contact details and company details
Core products: Business Mobile • Telephony • Internet • Business Energy Solutions

Brand & Visual Direction
We have a group logo currently tailored more toward telecoms, plus a separate Varnik Energy logo.
Please explore layouts that use both logos or just one, whichever works best.
Color: I wouldn't mind seeing an option using our the Blue/Purple gradient from our website (varnik-example.co.uk), but also open to non-gradient approaches and other colours..

Overall look: Smart, modern, and distinctive.
Format & Print Specs
Double-sided business card format. (Use a standard size

Must-Haves
Front: Varnik wording or Varnik Holdings wording with atleast 1 logo also on front “Business Communications | Business Energy.”

Back: Contact + company details and core products.
A design that stands out while remaining professional.

Nice-to-Have Options
A gradient version using our site’s Blue/Purple gradient.
A non-gradient version.
A dual-logo treatment versus a single-logo treatment.

Thanks
Owen

```html
<!DOCTYPE html>
<html lang="en">
<head>
<meta charset="utf-8">
<title>Varnik Holdings – Business Card</title>
<link href="https://fonts.googleapis.com/css2?family=Roboto:wght@400;700;900&display=swap" rel="stylesheet">
<style>
  :root {
    --page-bg: #f0f0f0;
    --card-bg: #ffffff;
    --navy: #25215e;
    --green: #2aa84a;
    --lime: #d6d62a;
    --blue: #2f6fc0;
    --white: #ffffff;
  }
  * { margin: 0; padding: 0; box-sizing: border-box; }
  html, body {
    width: 1200px; height: 990px; overflow: hidden;
    background: var(--page-bg);
    font-family: "Roboto", Arial, sans-serif;
  }
  .card {
    position: absolute; left: 244px; width: 712px; height: 406px;
    background: var(--card-bg); overflow: hidden;
    box-shadow: 0 10px 30px rgba(0,0,0,0.28);
  }
  .card-front { top: 68px; }
  .card-back  { top: 516px; }

  /* Front */
  .front-brand {
    position: absolute; left: 0; right: 0; top: 150px;
    display: flex; justify-content: center; align-items: center; gap: 22px;
  }
  .brand-dot {
    width: 70px; height: 70px; border-radius: 50%;
    background: var(--green);
  }
  .front-name {
    font-weight: 900; font-size: 84px; color: var(--navy); letter-spacing: 1px; line-height: 1;
  }
  .front-descriptor {
    position: absolute; left: 0; right: 0; top: 354px;
    text-align: center; font-size: 19px; color: var(--navy); letter-spacing: 0.5px;
  }

  /* Back */
  .back-gradient {
    position: absolute; inset: 0;
    background: linear-gradient(90deg, var(--green) 0%, var(--lime) 100%);
    clip-path: polygon(0 0, 490px 0, 465px 406px, 0 406px);
  }
  .back-brand {
    position: absolute; left: 30px; top: 40px;
    display: flex; align-items: center; gap: 12px;
  }
  .back-brand .brand-dot { width: 44px; height: 44px; background: var(--white); }
  .back-name {
    font-weight: 900; font-size: 38px; color: var(--white); letter-spacing: 0.5px; line-height: 1;
  }
  .name-marker {
    position: absolute; left: 0; top: 160px; width: 12px; height: 45px; background: var(--white);
  }
  .contact {
    position: absolute; left: 25px; top: 158px; color: var(--white);
  }
  .person-name { font-weight: 700; font-size: 31px; line-height: 1; }
  .person-role { font-size: 16px; margin-top: 2px; }
  .address { font-size: 16px; line-height: 22px; margin-top: 16px; letter-spacing: 0.4px; }
  .contact-list { list-style: none; margin-top: 6px; font-size: 16px; letter-spacing: 0.4px; }
  .contact-list li { display: flex; align-items: center; gap: 9px; height: 22px; }
  .contact-list svg { width: 14px; height: 14px; fill: var(--white); }
  .products { list-style: none; margin-top: 12px; font-size: 16px; letter-spacing: 0.3px; }
  .products li { height: 22px; }
  .products .dot { display: inline-block; width: 8px; height: 8px; border-radius: 50%; background: var(--white); margin: 0 6px 2px 0; vertical-align: middle; }

  .back-accent {
    position: absolute; left: 420px; top: 200px; width: 220px; height: 220px; border-radius: 50%;
    border: 18px solid var(--blue);
  }
  .vertical-name {
    position: absolute; left: 845px; top: 0;
    transform-origin: 0 0; transform: translate(-172px, 406px) rotate(-90deg);
    font-weight: 900; font-size: 104px; line-height: 1; color: var(--navy); letter-spacing: 2px;
    white-space: nowrap;
  }
</style>
</head>
<body>

<section class="card card-front" aria-label="Card front">
  <div class="front-brand">
    <span class="brand-dot"></span>
    <span class="front-name">VARNIK</span>
  </div>
  <p class="front-descriptor">Business Communications | Business Energy</p>
</section>

<section class="card card-back" aria-label="Card back">
  <div class="back-gradient"></div>

  <div class="back-brand">
    <span class="brand-dot"></span>
    <span class="back-name">VARNIK</span>
  </div>

  <span class="name-marker"></span>
  <div class="contact">
    <p class="person-name">Mira Kovalen</p>
    <p class="person-role">Founder &amp; CEO</p>
    <p class="address">24 Example Lane, Manchester,<br>England, M1 0XX</p>
    <ul class="contact-list">
      <li><svg viewBox="0 0 24 24"><path d="M6.6 10.8a15 15 0 0 0 6.6 6.6l2.2-2.2a1 1 0 0 1 1-.25 11.4 11.4 0 0 0 3.6.57 1 1 0 0 1 1 1V20a1 1 0 0 1-1 1A17 17 0 0 1 3 4a1 1 0 0 1 1-1h3.5a1 1 0 0 1 1 1c0 1.25.2 2.45.57 3.6a1 1 0 0 1-.25 1z"/></svg>+44 0161 000 0000</li>
      <li><svg viewBox="0 0 24 24"><path d="M12 2a10 10 0 1 0 0 20 10 10 0 0 0 0-20zm6.9 6h-2.9a15 15 0 0 0-1.4-3.6A8 8 0 0 1 18.9 8zM12 4c.8 1.2 1.5 2.5 1.9 4h-3.8c.4-1.5 1.1-2.8 1.9-4zM4.3 14a8 8 0 0 1 0-4h3.4a16 16 0 0 0 0 4zm.8 2h2.9c.3 1.3.8 2.5 1.4 3.6A8 8 0 0 1 5.1 16zM8 8H5.1a8 8 0 0 1 4.3-3.6C8.8 5.5 8.3 6.7 8 8zm4 12c-.8-1.2-1.5-2.5-1.9-4h3.8c-.4 1.5-1.1 2.8-1.9 4zm2.3-6H9.7a14 14 0 0 1 0-4h4.6a14 14 0 0 1 0 4zm.3 5.6c.6-1.1 1.1-2.3 1.4-3.6h2.9a8 8 0 0 1-4.3 3.6zm1.7-5.6a16 16 0 0 0 0-4h3.4a8 8 0 0 1 0 4z"/></svg>www.varnik-example.co.uk</li>
      <li><svg viewBox="0 0 24 24"><path d="M3 5h18a1 1 0 0 1 1 1v12a1 1 0 0 1-1 1H3a1 1 0 0 1-1-1V6a1 1 0 0 1 1-1zm1 2.4V17h16V7.4l-8 5.3z"/></svg>info@varnik-example.co.uk</li>
    </ul>
    <ul class="products">
      <li><span class="dot"></span>Business Mobile <span class="dot"></span>Telephony</li>
      <li><span class="dot"></span>Internet <span class="dot"></span>Business Energy Solutions</li>
    </ul>
  </div>

  <span class="back-accent"></span>
  <span class="vertical-name">VARNIK</span>
</section>

</body>
</html>
```